Business Cards for IT Consulting Company (Managed Service Provider)

I am looking to have some business cards printed and would like some designs. We are an IT Consulting company based in Vancouver BC. I would like a nice clean and modern look to the cards. I have uploaded all the versions of my logo so parts can be used as needed. Here is a snippit from our website homepage:

Quillbrook Networks Ltd. is an IT Solutions Partner located in Vancouver BC, Canada. We offer IT solutions and support to customers in the greater Vancouver Area. With expertise in Microsoft platforms, as well as Linux and Mac OSX and over 12 years experience in the IT industry, Quillbrook Networks is dedicated to offering our clients top quality service and products. We take pride in the solutions we offer our customers. The greatest compliment a client can give us is to recommend our services.

Quillbrook Networks Ltd. offers a wide range of IT services from onsite service to remote support and managed service solutions. This allows clients to choose the support path that best suits their company’s needs. Supporting many different sized companies from small to enterprise level over the past 12 years Quillbrook Networks has the experience and expertise needed to ensure things run smoothly. Allowing our clients to focus on doing business.

Revolutionizing the way IT services are delivered.

Quillbrook Networks is dedicated to providing our clients with IT solutions that work and grow with them for years to come. This philosophy helps save money in the long run instead of replacing equipment constantly. Far too often IT solutions are not well thought out and while possibly solving the problem at hand, require replacement due to growth or quality within a very short time frame. Quillbrook Networks takes pride in providing solutions that will last and be able to accommodate growth without the need for replacement.

Industry/Entity Type

Information Technology

Contact Information for Business Card

Quillbrook Networks Ltd.
(Employee Name)
Eml: (Employees Email Address)
Web: quillbrook.me
Ph: 604-555-0148

Font styles to use
Serif
Sans Serif

Requirements
Must have
• The Company logo and company colors.
Nice to have
• - Our tag line: "Revolutionizing IT Services" or "Revolutionizing the way IT services are delivered."
• - Also I really like the idea of nature and technology together blending which is sort of where my logo came from so integrating that somehow onto the business cards would be great.

```html
<!DOCTYPE html>
<html lang="en">
<head>
<meta charset="utf-8">
<title>Quillbrook Networks – Business Cards</title>
<link rel="stylesheet" href="https://fonts.googleapis.com/css2?family=Montserrat:wght@600&family=Source+Sans+3:ital,wght@0,400;0,600;1,600&display=swap">
<style>
  :root {
    --backdrop: #1a1a1a;
    --card: #ffffff;
    --brand-blue: #1aa3e0;
    --ink: #4a4a4c;
    --ink-dark: #222224;
    --rule: #d6d6d6;
  }
  * { margin: 0; padding: 0; box-sizing: border-box; }
  html, body { width: 1200px; height: 900px; overflow: hidden; }
  body {
    background: var(--backdrop);
    font-family: "Source Sans 3", Arial, sans-serif;
    position: relative;
  }
  .card {
    position: absolute;
    top: 306px;
    width: 440px;
    height: 271px;
    background: var(--card);
    border-radius: 10px;
    overflow: hidden;
  }
  .card--front { left: 149px; }
  .card--back { left: 608px; }

  /* front */
  .front-mark {
    position: absolute;
    left: 48px; top: 118px;
    display: flex; align-items: center; gap: 8px;
    color: var(--brand-blue);
    font-size: 22px; font-weight: 600;
  }
  .front-mark__square {
    width: 16px; height: 16px;
    border: 3px solid var(--brand-blue);
  }
  .divider {
    position: absolute;
    left: 204px; top: 74px;
    width: 1px; height: 148px;
    background: linear-gradient(to bottom, transparent, var(--rule) 25%, var(--rule) 75%, transparent);
  }
  .contact {
    position: absolute;
    left: 240px; top: 92px;
  }
  .contact__name {
    font-size: 17px; font-weight: 600;
    color: var(--ink);
    margin-bottom: 18px;
  }
  .contact__name .first { color: var(--brand-blue); }
  .contact__list { list-style: none; }
  .contact__list li {
    display: flex; align-items: center; gap: 5px;
    font-size: 12.5px; color: var(--ink-dark);
    height: 18px;
  }
  .contact__list svg { width: 9px; height: 9px; flex: none; }
  .tagline {
    position: absolute;
    left: 0; right: 0; top: 231px;
    display: flex; align-items: center; gap: 10px;
  }
  .tagline::before, .tagline::after {
    content: ""; flex: 1; height: 1.5px; background: var(--brand-blue);
  }
  .tagline__text {
    font-size: 15px; font-style: italic; font-weight: 600;
    color: var(--ink);
  }
  .tagline__text em { color: var(--brand-blue); font-style: italic; }

  /* back */
  .back-mark {
    position: absolute;
    left: 0; right: 0; top: 0; bottom: 0;
    display: flex; align-items: center; justify-content: center; gap: 14px;
  }
  .back-mark__circle {
    width: 46px; height: 46px; border-radius: 50%;
    background: var(--brand-blue);
  }
  .back-mark__name {
    font-family: "Montserrat", Arial, sans-serif;
    font-weight: 600;
    font-size: 30px;
    line-height: 1.1;
    color: var(--brand-blue);
  }
  .back-mark__name span { display: block; font-size: 15px; letter-spacing: 1px; }
</style>
</head>
<body>

  <section class="card card--front" aria-label="Business card front">
    <div class="front-mark">
      <span class="front-mark__square"></span>
      <span>Quillbrook</span>
    </div>
    <div class="divider"></div>
    <div class="contact">
      <p class="contact__name"><span class="first">Daniel</span> Moreau</p>
      <ul class="contact__list">
        <li>
          <svg viewBox="0 0 10 10" aria-hidden="true"><path d="M2 0.5 L3.6 2.6 L2.8 3.6 Q4 6 6.4 7.2 L7.4 6.4 L9.5 8 L8.4 9.5 Q4.5 9.5 0.5 1.6 Z" fill="var(--brand-blue)"/></svg>
          604-555-0148
        </li>
        <li>
          <svg viewBox="0 0 10 10" aria-hidden="true"><rect x="0.5" y="2" width="9" height="6.5" fill="var(--brand-blue)"/><path d="M0.8 2.3 L5 5.6 L9.2 2.3" fill="none" stroke="#fff" stroke-width="0.9"/></svg>
          info@quillbrook.me
        </li>
        <li>
          <svg viewBox="0 0 10 10" aria-hidden="true"><circle cx="5" cy="5" r="4.6" fill="var(--brand-blue)"/><path d="M3 3 Q4.5 4 3.6 5.6 M6 2 Q7.5 4.5 6.2 7.8" fill="none" stroke="#fff" stroke-width="0.9"/></svg>
          www.quillbrook.me
        </li>
      </ul>
    </div>
    <div class="tagline">
      <p class="tagline__text"><em>Revolutionizing</em> IT Services</p>
    </div>
  </section>

  <section class="card card--back" aria-label="Business card back">
    <div class="back-mark">
      <span class="back-mark__circle"></span>
      <p class="back-mark__name">quillbrook<span>NETWORKS LTD.</span></p>
    </div>
  </section>

</body>
</html>
```